Local Flower Farm Needs Business Card Design

I need business cards designed for a flower farm based in Eudora, Kansas.
Business Info:
We are a local cut flower farm located in Eudora, Kansas, founded by Corinne Haldwick. What started as a passion for agriculture and search for more joy in daily life has blossomed into a small business dedicated to providing the community with beautiful, fresh, and sustainable flowers. We specialize in local, seasonal blooms, ensuring that every petal reflects the care and dedication we pour into our craft. Our mission is to deliver the highest quality flowers directly to our customers through local farmers markets and to florists who share our commitment to sustainability. Join us in celebrating the beauty of nature, one bloom at a time!
Contact Details:
Corinne Haldwick
Owner
Phone 913-555-0147
Facebook: Rosalind Thorpe Gardens
Instagram: @RosalindThorpeGardens
Website: RosalindThorpeGardens.example
Target Market(s)
Wholesale to Florists and Direct to Consumer via Farmers Market
Industry/Entity Type
Florist, Farm
Contact Information for Business Card
Name, Contact Info, Logo
Look and feel
Each slider illustrates characteristics of the customer's brand and the style your logo design should communicate.

```html
<!DOCTYPE html>
<html lang="en">
<head>
<meta charset="utf-8">
<title>Rosalind Thorpe Gardens — Business Card</title>
<link rel="stylesheet" href="https://fonts.googleapis.com/css2?family=Libre+Baskerville:wght@400;700&display=swap">
<style>
  :root {
    --stage: #141618;
    --card-light: #0a2d34;
    --card-dark: #071a1e;
    --ink-white: #ffffff;
    --ink-teal: #0b2a30;
  }
  * { margin: 0; padding: 0; box-sizing: border-box; }
  html, body { width: 1200px; height: 840px; overflow: hidden; }
  body {
    background: var(--stage);
    font-family: "Libre Baskerville", "Times New Roman", serif;
    color: var(--ink-white);
    display: flex;
    flex-direction: column;
    align-items: center;
    justify-content: center;
    gap: 60px;
  }
  .card {
    position: relative;
    width: 560px;
    height: 320px;
    border-radius: 24px;
    background: linear-gradient(135deg, var(--card-light) 0%, var(--card-dark) 55%, var(--card-light) 100%);
    overflow: hidden;
  }

  /* Front */
  .front-seal {
    position: absolute;
    left: 50%; top: 50%;
    width: 230px; height: 230px;
    transform: translate(-50%, -50%);
    border-radius: 50%;
    background: var(--ink-white);
    display: flex;
    align-items: center;
    justify-content: center;
    text-align: center;
    color: var(--ink-teal);
    font-size: 21px;
    line-height: 1.35;
    letter-spacing: 0.08em;
    text-transform: uppercase;
  }

  /* Back */
  .back-seal {
    position: absolute;
    left: 50%; top: 22px;
    transform: translateX(-50%);
    width: 150px; height: 150px;
    border-radius: 50%;
    border: 1.5px solid var(--ink-white);
    display: flex;
    align-items: center;
    justify-content: center;
    text-align: center;
    font-size: 14px;
    line-height: 1.35;
    letter-spacing: 0.08em;
    text-transform: uppercase;
  }
  .person {
    position: absolute;
    left: 20px; top: 232px;
    width: 226px;
    text-align: right;
  }
  .person-name {
    font-weight: 700;
    font-size: 16px;
    letter-spacing: 0.02em;
    text-transform: uppercase;
    white-space: nowrap;
  }
  .person-title { font-size: 13px; margin-top: 3px; }
  .divider {
    position: absolute;
    left: 258px; top: 196px;
    width: 1px; height: 104px;
    background: var(--ink-white);
  }
  .contact-list {
    position: absolute;
    left: 272px; top: 198px;
    list-style: none;
    font-size: 13px;
    line-height: 25px;
  }
  .contact-list li { display: flex; align-items: center; gap: 9px; white-space: nowrap; }
  .contact-icon { width: 14px; height: 14px; flex: none; }
</style>
</head>
<body>

  <section class="card card-front" aria-label="Card front">
    <div class="front-seal">Rosalind<br>Thorpe<br>Gardens</div>
  </section>

  <section class="card card-back" aria-label="Card back">
    <div class="back-seal">Rosalind<br>Thorpe<br>Gardens</div>

    <div class="person">
      <p class="person-name">Corinne Haldwick</p>
      <p class="person-title">Owner</p>
    </div>

    <div class="divider"></div>

    <ul class="contact-list">
      <li>
        <svg class="contact-icon" viewBox="0 0 16 16" aria-hidden="true">
          <path fill="#fff" d="M4 2l2.5 0 1 3-1.6 1.2a8 8 0 0 0 3.9 3.9L11 8.5l3 1V12a2 2 0 0 1-2 2C6.5 14 2 9.5 2 4a2 2 0 0 1 2-2z"/>
        </svg>
        913-555-0147
      </li>
      <li>
        <svg class="contact-icon" viewBox="0 0 16 16" aria-hidden="true">
          <rect x="2" y="2" width="12" height="12" fill="#fff"/>
        </svg>
        Rosalind Thorpe Gardens
      </li>
      <li>
        <svg class="contact-icon" viewBox="0 0 16 16" aria-hidden="true">
          <rect x="2" y="2" width="12" height="12" fill="#fff"/>
        </svg>
        @RosalindThorpeGardens
      </li>
      <li>
        <svg class="contact-icon" viewBox="0 0 16 16" aria-hidden="true">
          <circle cx="8" cy="8" r="6.2" fill="none" stroke="#fff" stroke-width="1.4"/>
          <ellipse cx="8" cy="8" rx="2.6" ry="6.2" fill="none" stroke="#fff" stroke-width="1.2"/>
          <line x1="1.8" y1="8" x2="14.2" y2="8" stroke="#fff" stroke-width="1.2"/>
        </svg>
        RosalindThorpeGardens.example
      </li>
    </ul>
  </section>

</body>
</html>
```